Quillfern Vaults - Direct Mailer / Flyer

We are excited to announce the launch of our new company, Quillfern Vaults, a premier cohosting facility and data center dedicated to Cryptocurrency Miners. Our website, https://quillfernvaults.example, provides detailed information about our offerings and showcases the innovative design schemes for the entire project.

Quillfern Vaults stands out in the industry by offering both GPU Hosting and ASIC Hosting services in our state-of-the-art facility, equipped with an impressive 17 Megawatts of available power. What sets us apart is our unique billing system based on actual metered power usage. We charge $0.08 for ASIC miners and $0.09 for GPU miners, ensuring cost-effectiveness and transparency for our clients.

Our commitment to excellence is evident in our use of cutting-edge technology, top-notch facilities, and strategic partnerships. These elements come together to deliver exceptional solutions tailored for real-world applications in the cryptocurrency space.

As part of our promotional efforts, we are developing a direct mailer/flyer to introduce Quillfern Vaults to a wider audience. This promotional material will also serve as a handout at events, to potential customers, and more. We welcome creative ideas and suggestions to maximize the versatility of this design and reach diverse target audiences effectively.

For a comprehensive overview of our services and to explore our design concepts, please visit https://quillfernvaults.example. Quillfern Vaults is poised to revolutionize the mining industry, and we look forward to partnering with you for success in the digital currency era.

```html
<!DOCTYPE html>
<html lang="en">
<head>
<meta charset="utf-8">
<title>Quillfern Vaults – Cohosting Flyer</title>
<link href="https://fonts.googleapis.com/css2?family=Oswald:wght@500;600&family=Lato:wght@400&display=swap" rel="stylesheet">
<style>
  :root {
    --yellow: #f2f55a;
    --cyan: #6ffcfa;
    --slate: #595553;
    --ink: #1e1e1e;
    --paper: #ffffff;
    --backdrop: #f3f3f3;
    --rule: #3fa7b3;
  }
  * { margin: 0; padding: 0; box-sizing: border-box; }
  html, body { width: 1200px; height: 841px; overflow: hidden; background: var(--backdrop); }
  body { position: relative; font-family: "Lato", sans-serif; color: var(--ink); }

  .page {
    position: absolute; top: 20px; width: 566px; height: 800px;
    background: var(--paper); overflow: hidden;
    box-shadow: 0 1px 4px rgba(0,0,0,.12);
  }
  .page--front { left: 18px; }
  .page--back { left: 616px; }
  .page__art { position: absolute; inset: 0; width: 566px; height: 800px; }

  .heading { font-family: "Oswald", sans-serif; font-weight: 500; line-height: 1; position: absolute; }

  /* front */
  .brand {
    position: absolute; left: 255px; top: 470px; width: 180px;
    display: flex; align-items: center; justify-content: center; gap: 5px;
    font-family: "Oswald", sans-serif; font-weight: 600; font-size: 16px;
    text-transform: uppercase; letter-spacing: .3px; color: var(--ink);
  }
  .brand__mark { width: 14px; height: 12px; background: var(--ink); }
  .front-title { left: 30px; top: 566px; font-size: 38px; line-height: 48px; color: #fff; white-space: nowrap; }
  .front-lede { position: absolute; left: 32px; top: 685px; font-size: 13.2px; line-height: 23.5px; color: #fff; }
  .front-rule { position: absolute; left: 33px; top: 753px; width: 79px; height: 1px; background: var(--rule); }
  .call { position: absolute; left: 393px; top: 732px; font-family: "Oswald", sans-serif; }
  .call__label { font-size: 12.5px; font-weight: 500; }
  .call__number { font-size: 22px; font-weight: 500; margin-top: 2px; }

  /* back */
  .service { position: absolute; left: 96px; width: 170px; }
  .service__title { font-family: "Oswald", sans-serif; font-weight: 500; font-size: 18.5px; line-height: 1; }
  .service__text { font-size: 7.4px; line-height: 12.4px; margin-top: 7px; }
  .back-title { left: 303px; top: 90px; font-size: 30.5px; line-height: 38px; white-space: nowrap; }
  .back-lede { position: absolute; left: 304px; top: 199px; width: 250px; font-size: 11.4px; line-height: 18.2px; }
  .stat { position: absolute; left: 375px; }
  .stat__value { font-size: 20px; line-height: 1; }
  .stat__label { font-size: 8.4px; margin-top: 5px; }
  .contact-title { right: 82px; top: 624px; font-size: 23px; color: #fff; }
  .contact-rule { position: absolute; left: 440px; top: 654px; width: 44px; height: 2px; background: #fff; }
  .contact-line { position: absolute; right: 115px; font-size: 10.4px; line-height: 13px; color: #fff; text-align: left; white-space: nowrap; }
</style>
</head>
<body>

<section class="page page--front">
  <svg class="page__art" viewBox="0 0 566 800">
    <defs>
      <linearGradient id="coinScene" x1="0" y1="0" x2="1" y2="1">
        <stop offset="0" stop-color="#3a2a17"/>
        <stop offset=".45" stop-color="#8a6433"/>
        <stop offset=".7" stop-color="#2a2a26"/>
        <stop offset="1" stop-color="#0f1a1e"/>
      </linearGradient>
      <linearGradient id="hallScene" x1="0" y1="0" x2="0" y2="1">
        <stop offset="0" stop-color="#0b2d57"/>
        <stop offset=".5" stop-color="#2a7fc9"/>
        <stop offset="1" stop-color="#0a3b6b"/>
      </linearGradient>
    </defs>
    <path d="M79,275 H170 C150,330 170,400 210,435 H150 C100,410 75,340 79,275 Z" fill="var(--cyan)"/>
    <path role="img" aria-label="Photo: gold coin resting on a laptop keyboard" d="M300,0 H566 V434 H255 C185,420 150,355 160,275 L240,275 C300,275 330,230 345,150 Z" fill="url(#coinScene)"/>
    <path d="M0,0 H350 L320,170 C300,250 270,280 220,283 H0 Z" fill="#e1e1e1"/>
    <path role="img" aria-label="Photo: server hall lit in blue" d="M0,0 H340 L310,165 C292,240 262,266 215,267 H0 Z" fill="url(#hallScene)"/>
    <rect x="434" y="443" width="132" height="53" fill="var(--cyan)"/>
    <path d="M0,469 H300 L366,580 L288,800 H0 Z" fill="var(--slate)"/>
    <path d="M322,706 H566 V800 H298 Z" fill="var(--yellow)"/>
    <circle cx="344" cy="481" r="99" fill="#fff"/>
    <circle cx="344" cy="481" r="89" fill="var(--yellow)"/>
    <g fill="none" stroke="var(--ink)" stroke-width="0.9">
      <circle cx="366" cy="755" r="17"/>
      <path d="M360,748 c-2,2 -1,6 2,9 c3,3 7,4 9,2 l1,-1.5 l-3,-2.5 l-2,1.5 c-1.5,-1 -3,-2.5 -4,-4 l1.5,-2 l-2.5,-3 Z"/>
      <path d="M367,746 a7,7 0 0 1 6,6 M367,749 a4,4 0 0 1 3,3"/>
    </g>
  </svg>

  <div class="brand"><span class="brand__mark"></span>Quillfern Vaults</div>

  <h1 class="heading front-title">Transform Mining<br>With Cohosting</h1>
  <p class="front-lede">Miners deserve the best - choose the hosting<br>company that delivers excellence!</p>
  <div class="front-rule"></div>

  <div class="call">
    <div class="call__label">Call Us</div>
    <div class="call__number">+1 (555) 014 2290</div>
  </div>
</section>

<section class="page page--back">
  <svg class="page__art" viewBox="0 0 566 800">
    <defs>
      <radialGradient id="fanScene" cx=".45" cy=".55" r=".7">
        <stop offset="0" stop-color="#7a4a16"/>
        <stop offset=".5" stop-color="#2c2a27"/>
        <stop offset="1" stop-color="#10191d"/>
      </radialGradient>
      <filter id="lift" x="-30%" y="-30%" width="160%" height="160%">
        <feDropShadow dx="0" dy="1" stdDeviation="2" flood-color="#000" flood-opacity=".15"/>
      </filter>
    </defs>

    <g fill="var(--yellow)">
      <circle cx="48" cy="77" r="28"/>
      <circle cx="48" cy="165" r="28"/>
      <circle cx="48" cy="252" r="28"/>
      <circle cx="48" cy="338" r="28"/>
    </g>
    <g fill="none" stroke="var(--ink)" stroke-width="0.9">
      <rect x="38" y="67" width="20" height="20" rx="1.5"/>
      <rect x="42" y="71" width="12" height="12"/>
      <path d="M42,63v4M46,63v4M50,63v4M54,63v4M42,87v4M46,87v4M50,87v4M54,87v4M34,71h4M34,77h4M34,83h4M58,71h4M58,77h4M58,83h4"/>
      <rect x="37" y="154" width="22" height="22" rx="3"/>
      <circle cx="48" cy="165" r="8"/><circle cx="48" cy="165" r="4.5"/><circle cx="48" cy="165" r="1.5"/>
      <rect x="35" y="253" width="26" height="12" rx="1.5"/>
      <circle cx="43" cy="259" r="4.5"/><circle cx="53" cy="259" r="4.5"/>
      <circle cx="44" cy="245" r="3.5"/><circle cx="52" cy="245" r="3.5"/>
      <path d="M34,349 h28 M38,349 v-8 h20 v8 M48,329 v-3 M43,320 h10 v6 h-10 Z"/>
      <circle cx="48" cy="334" r="3.5"/>
    </g>

    <circle cx="333" cy="328" r="26" fill="#fff" filter="url(#lift)"/>
    <circle cx="333" cy="402" r="26" fill="#fff" filter="url(#lift)"/>
    <g fill="none" stroke="#3b5bd6" stroke-width="0.9">
      <rect x="324" y="316" width="11" height="15" rx="1.5"/>
      <rect x="326" y="319" width="7" height="5"/>
      <path d="M330,331 v6 a4,4 0 0 0 8,0 v-9 M336,326 v4 M340,326 v4"/>
    </g>
    <g fill="none" stroke="#2a9a3c" stroke-width="0.9">
      <path d="M327,400 a6,6 0 1 1 12,0 c0,3 -3,5 -3,8 h-6 c0,-3 -3,-5 -3,-8 Z M330,411 h6 M331,414 h4"/>
      <path d="M333,404 v-6 l2,-2 M324,394 l-3,-2 M342,394 l3,-2 M333,389 v-3 M322,401 h-3 M344,401 h3"/>
    </g>

    <path d="M0,413 H215 C265,413 300,450 313,495 L300,497 C285,470 255,458 215,458 H0 Z" fill="var(--cyan)"/>
    <path d="M0,465 H222 C295,465 339,518 339,590 V800 H0 Z" fill="#fff"/>
    <path role="img" aria-label="Photo: rows of mining rigs with glowing fans" d="M0,469 H220 C290,469 335,520 335,590 V800 H0 Z" fill="url(#fanScene)"/>
    <path d="M343,563 H470 C530,563 565,620 555,690 L529,800 H281 Z" fill="var(--slate)"/>
    <path d="M343,563 L281,800" stroke="#fff" stroke-width="4"/>

    <g fill="var(--yellow)">
      <circle cx="473" cy="685" r="11.5"/>
      <circle cx="473" cy="719" r="11.5"/>
      <circle cx="473" cy="755" r="11.5"/>
    </g>
    <g fill="var(--ink)">
      <path d="M468.5,680.5 c-1,2 0,5 2.5,7.5 c2.5,2.5 5.5,3.5 7.5,2.5 l0.5,-2 l-2.8,-1.5 l-1.3,1.3 c-1.6,-.8 -3,-2.2 -3.8,-3.8 l1.3,-1.3 l-1.5,-2.8 Z"/>
      <rect x="467.5" y="715" width="11" height="8" rx="1"/>
      <path d="M473,749 a4,4 0 0 1 4,4 c0,3 -4,7 -4,7 c0,0 -4,-4 -4,-7 a4,4 0 0 1 4,-4 Z"/>
    </g>
    <path d="M468,716 l5,3.6 l5,-3.6" stroke="var(--yellow)" stroke-width="0.8" fill="none"/>
    <circle cx="473" cy="753" r="1.4" fill="var(--yellow)"/>
  </svg>

  <div class="service" style="top:46px">
    <h2 class="service__title">GPU Hosting</h2>
    <p class="service__text">Begin your GPU Hosting journey with rates starting at $0.09 kWh, accepting all equipment.</p>
  </div>
  <div class="service" style="top:140px">
    <h2 class="service__title">ASIC Hosting</h2>
    <p class="service__text">Get your ASICs directly from us or send yours in today, starting at an all-in rate of $0.08 kWh.</p>
  </div>
  <div class="service" style="top:227px">
    <h2 class="service__title">Mining Hardware</h2>
    <p class="service__text">Looking for mining hardware? Our equipment comes with no additional markup, ever.</p>
  </div>
  <div class="service" style="top:313px">
    <h2 class="service__title">Crypto Consulting</h2>
    <p class="service__text">Enjoy complete White Glove Services for setup, insurance, and tax consulting.</p>
  </div>

  <h2 class="heading back-title">Real Solutions<br>For Real Applications</h2>
  <p class="back-lede">Quillfern Vaults has committed to leveraging cutting-edge technology, state-of-the-art facilities, and strategic partnerships to deliver exceptional solutions tailored for real-world applications in the cryptocurrency space.</p>

  <div class="stat" style="top:312px">
    <div class="stat__value">4,000,000+</div>
    <div class="stat__label">watts available for hosting</div>
  </div>
  <div class="stat" style="top:386px">
    <div class="stat__value">2,000,000+</div>
    <div class="stat__label">watts of green energy being produced</div>
  </div>

  <h2 class="heading contact-title">Contact us</h2>
  <div class="contact-rule"></div>
  <p class="contact-line" style="top:679px">+1 (555) 014 2290</p>
  <p class="contact-line" style="top:713px">info@quillfernvaults.example</p>
  <p class="contact-line" style="top:743px">Lorem ipsum dolor<br>sit amet</p>
</section>

</body>
</html>
```